Dalvick's Business Card

I need some designs for a new business card including the new logo attached. An old example of our business card is also attached to show all the data that should be included on the new design.
**I added some more examples someone had mocked up**

Contact Information for Business Card

Should include all info on other examples uploaded.

```html
<!DOCTYPE html>
<html lang="en">
<head>
<meta charset="utf-8">
<title>Dalvick's Business Card</title>
<link rel="stylesheet" href="https://fonts.googleapis.com/css2?family=Poppins:wght@400;500;700;800&display=swap">
<style>
  :root {
    --brand-blue: #0870c0;
    --brand-red: #ec1c24;
    --card-white: #ffffff;
    --backdrop: #202020;
  }
  html, body {
    margin: 0;
    padding: 0;
    width: 1200px;
    height: 1015px;
    overflow: hidden;
    background: var(--backdrop);
    font-family: "Poppins", sans-serif;
  }
  .canvas {
    position: relative;
    width: 1200px;
    height: 1015px;
  }
  .card {
    position: absolute;
    left: 300px;
    width: 600px;
    height: 343px;
    background: var(--card-white);
    overflow: hidden;
    box-shadow: 0 14px 30px rgba(0,0,0,0.6);
  }
  .card--back { top: 118px; }
  .card--front { top: 534px; }
  .card svg.wave {
    position: absolute;
    inset: 0;
    width: 600px;
    height: 343px;
  }
  .wordmark {
    position: absolute;
    display: flex;
    align-items: center;
    gap: 12px;
    font-weight: 800;
    color: var(--brand-blue);
    letter-spacing: 1px;
    line-height: 1;
  }
  .wordmark__dot {
    width: 34px;
    height: 34px;
    border-radius: 50%;
    background: var(--brand-red);
  }
  .card--back .wordmark { right: 40px; top: 212px; font-size: 50px; }
  .card--front .wordmark { left: 40px; top: 92px; font-size: 50px; }

  .service-area {
    position: absolute;
    left: 34px;
    top: 40px;
    color: var(--card-white);
  }
  .service-area__region {
    margin: 0 0 10px;
    font-size: 14px;
    font-weight: 500;
    letter-spacing: 0.6px;
  }
  .service-area__call {
    margin: 0;
    font-size: 17px;
    font-weight: 800;
    line-height: 1.15;
    letter-spacing: 0.4px;
    text-transform: uppercase;
  }

  .contact {
    position: absolute;
    right: 28px;
    top: 142px;
    text-align: right;
    color: var(--card-white);
  }
  .contact__name {
    margin: 0 0 8px;
    font-size: 22px;
    font-weight: 800;
    letter-spacing: 0.6px;
    text-transform: uppercase;
  }
  .contact__line {
    display: flex;
    justify-content: flex-end;
    align-items: center;
    gap: 8px;
    margin: 0 0 4px;
    font-size: 15px;
    font-weight: 400;
  }
  .contact__icon { width: 16px; height: 16px; flex: none; }
  .contact__tagline {
    margin: 14px 0 0;
    font-size: 15px;
    font-weight: 800;
    text-transform: uppercase;
    letter-spacing: 0.4px;
  }
  .credentials {
    position: absolute;
    left: 34px;
    bottom: 28px;
    margin: 0;
    color: var(--card-white);
    font-size: 17px;
    font-weight: 800;
    text-transform: uppercase;
    letter-spacing: 0.4px;
  }
</style>
</head>
<body>
<main class="canvas">

  <section class="card card--back" aria-label="Card back">
    <svg class="wave" viewBox="0 0 600 343" aria-hidden="true">
      <path fill="var(--brand-blue)" d="M0 0 H600 V100 C520 92 470 105 395 165 C315 230 200 262 40 270 H0 Z"/>
      <path fill="none" stroke="var(--brand-red)" stroke-width="7" d="M60 268 C210 260 315 228 392 168 C468 108 518 96 600 100"/>
      <path fill="none" stroke="var(--brand-red)" stroke-width="5" d="M240 246 C300 225 350 200 400 162 C470 112 525 104 600 112"/>
    </svg>
    <div class="service-area">
      <p class="service-area__region">Serves Millbrook, IA &amp; Surrounding Areas</p>
      <p class="service-area__call">Call today for all your HVAC<br>refrigeration &amp; plumbing needs</p>
    </div>
    <div class="wordmark"><span class="wordmark__dot"></span>DALVICK'S</div>
  </section>

  <section class="card card--front" aria-label="Card front">
    <svg class="wave" viewBox="0 0 600 343" aria-hidden="true">
      <path fill="var(--brand-blue)" d="M0 343 V262 C150 268 240 250 320 180 C400 110 480 92 600 92 V343 Z"/>
      <path fill="none" stroke="var(--brand-red)" stroke-width="7" d="M0 244 C140 250 230 232 312 166 C392 100 470 80 560 76"/>
      <path fill="none" stroke="var(--brand-red)" stroke-width="5" d="M0 256 C150 262 238 244 318 176 C340 158 360 142 380 130"/>
    </svg>
    <div class="wordmark"><span class="wordmark__dot"></span>DALVICK'S</div>
    <div class="contact">
      <p class="contact__name">Mark Dalvick</p>
      <p class="contact__line">555.014.2387
        <svg class="contact__icon" viewBox="0 0 16 16" aria-hidden="true"><path fill="var(--brand-red)" d="M3.5 1.5l2.5 3-1.4 1.6c.8 1.8 2 3 3.8 3.8L10 8.5l3 2.5-1.6 2.6C6.5 13.2 2.8 9.5 1.5 4.1z"/></svg>
      </p>
      <p class="contact__line">hvacdalvick@mailbox.com
        <svg class="contact__icon" viewBox="0 0 16 16" aria-hidden="true"><rect x="1" y="3" width="14" height="10" fill="var(--brand-red)"/><path d="M1 3l7 6 7-6" fill="none" stroke="var(--card-white)" stroke-width="1.2"/></svg>
      </p>
      <p class="contact__tagline">Family owned &amp; operated</p>
    </div>
    <p class="credentials">Licensed &amp; Insured</p>
  </section>

</main>
</body>
</html>
```